Company identity deisgn should support 2 languages

I would like to get our company identity design
This includes the following only
Business Cards 2 languages Arabic and English
Email signature
Letterhead
Linkedin profile images
Attached is the logo in Ai format

Requirements
Must have
• For business card
Must have
Name and Adrees in arabic
Name and Address in english
You might use both side of the card
Should not have
• Any pictures other than the logo

```html
<!DOCTYPE html>
<html lang="en">
<head>
<meta charset="utf-8">
<title>Lumenra Systems — Stationery</title>
<link rel="stylesheet" href="https://fonts.googleapis.com/css2?family=Oswald:wght@300;400;500&family=Cairo:wght@400;600&display=swap">
<style>
  :root {
    --backdrop: #999999;
    --paper: #ffffff;
    --ink: #6d6d6d;
    --ink-strong: #5a5a5a;
    --ink-soft: #9a9a9a;
    --brand-blue: #1f78c1;
    --decor: #d6d6d6;
  }
  * { margin: 0; padding: 0; box-sizing: border-box; }
  html, body { width: 1200px; height: 1200px; overflow: hidden; }
  body {
    background: var(--backdrop);
    font-family: "Oswald", "Arial Narrow", sans-serif;
    font-weight: 300;
    color: var(--ink);
    position: relative;
  }
  .sheet, .card {
    position: absolute;
    background: var(--paper);
    overflow: hidden;
    box-shadow: 0 1px 4px rgba(0,0,0,.15);
  }
  .corner-decor {
    position: absolute;
    border-radius: 50%;
    background: var(--decor);
  }
  .wordmark {
    position: absolute;
    display: flex;
    align-items: center;
    gap: 8px;
    color: var(--brand-blue);
    font-weight: 400;
    letter-spacing: .08em;
    white-space: nowrap;
  }
  .wordmark .dot { border-radius: 50%; background: var(--brand-blue); flex: none; }

  /* Letterhead */
  .letterhead { left: 60px; top: 140px; width: 654px; height: 926px; }
  .letterhead .wordmark { left: 39px; top: 60px; font-size: 24px; }
  .letterhead .wordmark .dot { width: 22px; height: 22px; }
  .letter-body { position: absolute; left: 64px; width: 526px; font-size: 9.6px; line-height: 15.5px; }
  .letter-body p { position: absolute; left: 0; width: 526px; text-align: justify; }
  .salutation { font-size: 10.5px; }
  .signer-name { position: absolute; left: 64px; top: 720px; font-weight: 500; color: var(--ink-strong); font-size: 10.5px; }
  .signer-role { position: absolute; left: 64px; top: 735px; font-size: 9.5px; }
  .letter-footer { position: absolute; left: 39px; top: 828px; }
  .letter-footer .contact { font-size: 12.5px; line-height: 17px; }
  .letter-footer .company { font-weight: 500; color: var(--ink-strong); font-size: 10.5px; margin-top: 4px; }
  .letter-footer .address { font-size: 9.5px; margin-top: 1px; }
  .letterhead .corner-decor { width: 320px; height: 320px; right: -90px; bottom: -110px; }

  /* Cards */
  .card { left: 779px; width: 372px; height: 218px; }
  .card-en { top: 242px; }
  .card-ar { top: 528px; }
  .card .wordmark { right: 28px; top: 38px; font-size: 14px; }
  .card .wordmark .dot { width: 13px; height: 13px; }
  .card-name { position: absolute; left: 22px; top: 30px; font-size: 12.5px; font-weight: 400; color: var(--ink-strong); }
  .card-role { position: absolute; left: 22px; top: 48px; font-size: 9.5px; }
  .card-contact { position: absolute; left: 22px; top: 116px; font-size: 8.3px; line-height: 13px; }
  .card-contact .phone { font-size: 9.5px; }
  .card-company { position: absolute; left: 22px; top: 178px; font-size: 8.8px; font-weight: 500; color: var(--ink-strong); }
  .card-address { position: absolute; left: 22px; top: 191px; font-size: 8.3px; }
  .card .corner-decor { width: 150px; height: 150px; right: -35px; bottom: -60px; }
  .arabic { font-family: "Cairo", "Tahoma", sans-serif; font-weight: 400; direction: rtl; text-align: left; }
  .card-ar .card-name { font-size: 12px; top: 26px; }
  .card-ar .card-role { color: var(--ink-soft); font-size: 8.5px; top: 44px; }
  .card-ar .card-company { font-size: 7.5px; font-weight: 600; top: 176px; }
  .card-ar .card-address { color: var(--ink-soft); font-size: 7.3px; top: 190px; }
</style>
</head>
<body>

<section class="sheet letterhead">
  <div class="wordmark"><span class="dot"></span>LUMENRA SYSTEMS</div>

  <div class="letter-body">
    <p class="salutation" style="top:188px">Dear Sir</p>
    <p style="top:218px">Lorem ipsum dolor sit amet, consetetur sadipscing elitr, sed diam nonumy eirmod tempor invidunt ut labore et dolore magna aliquyam erat, sed diam voluptua. At vero eos et accusam et justo duo dolores et ea rebum. Stet clita kasd gubergren, no sea takimata sanctus est Lorem ipsum dolor sit amet. Lorem ipsum dolor sit amet, consetetur sadipscing elitr, sed diam nonumy eirmod tempor invidunt ut labore et dolore magna aliquyam erat, sed diam voluptua. At vero eos et accusam et justo duo dolores et ea rebum. Stet clita kasd gubergren, no sea takimata sanctus est Lorem ipsum dolor sit amet. Lorem ipsum dolor sit amet, consetetur sadipscing elitr, sed diam nonumy eirmod tempor invidunt ut labore et dolore magna aliquyam erat, sed diam voluptua. At vero eos et accusam et justo duo dolores et ea rebum. Stet clita kasd gubergren, no sea takimata sanctus est Lorem ipsum dolor sit amet. Duis autem vel eum iriure dolor in hendrerit in vulputate velit esse molestie consequat, vel illum dolore eu feugiat nulla facilisis at vero eros et accumsan et iusto odio dignissim qui blandit praesent luptatum zzril delenit augue duis dolore te feugait nulla facilisi. Lorem ipsum dolor sit amet, consectetuer adipiscing elit, sed diam nonummy nibh euismod tincidunt ut laoreet dolore magna aliquam erat volutpat.</p>
    <p style="top:357px">Ut wisi enim ad minim veniam, quis nostrud exerci tation ullamcorper suscipit lobortis nisl ut aliquip ex ea commodo consequat. Duis autem vel eum iriure dolor in hendrerit in vulputate velit esse molestie consequat, vel illum dolore eu feugiat nulla facilisis at vero eros et accumsan et iusto odio dignissim qui blandit praesent luptatum zzril delenit augue duis dolore te feugait nulla facilisi. Nam liber tempor cum soluta nobis eleifend option congue nihil imperdiet doming id quod mazim placerat facer possim assum. Lorem ipsum dolor sit amet, consectetuer adipiscing elit, sed diam nonummy nibh euismod tincidunt ut laoreet dolore magna aliquam erat volutpat. Ut wisi enim ad minim veniam, quis nostrud exerci tation ullamcorper suscipit lobortis nisl ut aliquip ex ea commodo consequat. Duis autem vel eum iriure dolor in hendrerit in vulputate velit esse molestie consequat, vel illum dolore eu feugiat nulla facilisis.</p>
    <p style="top:465px">At vero eos et accusam et justo duo dolores et ea rebum. Stet clita kasd gubergren, no sea takimata sanctus est Lorem ipsum dolor sit amet. Lorem ipsum dolor sit amet, consetetur sadipscing elitr, sed diam nonumy eirmod tempor invidunt ut labore et dolore magna aliquyam erat, sed diam voluptua. At vero eos et accusam et justo duo dolores et ea rebum. Stet clita kasd gubergren, no sea takimata sanctus est Lorem ipsum dolor sit amet. Lorem ipsum dolor sit amet, consetetur sadipscing elitr, At accusam aliquyam diam diam dolore dolores duo eirmod eos erat, et nonumy sed tempor et et invidunt justo labore Stet clita ea et gubergren, kasd magna no rebum. sanctus sea sed takimata ut vero voluptua. est Lorem ipsum dolor sit amet. Lorem ipsum dolor sit amet, consetetur sadipscing elitr, sed diam nonumy eirmod tempor invidunt ut labore et dolore magna aliquyam erat.</p>
    <p style="top:573px">Consetetur sadipscing elitr, sed diam nonumy eirmod tempor invidunt ut labore et dolore magna aliquyam erat, sed diam voluptua. At vero eos et accusam et justo duo dolores et ea rebum. Stet clita kasd gubergren, no sea takimata sanctus est Lorem ipsum dolor sit amet. Lorem ipsum dolor sit amet, consetetur sadipscing elitr, sed diam nonumy eirmod tempor invidunt ut labore et dolore magna aliquyam erat, sed diam voluptua. At vero eos et accusam et justo duo dolores et ea rebum. Stet clita kasd gubergren, no sea takimata sanctus est Lorem ipsum dolor sit amet. Lorem ipsum dolor sit amet, consetetur sadipscing elitr, sed diam nonumy eirmod tempor invidunt ut labore et dolore magna aliquyam erat, sed diam voluptua. At vero eos et accusam et justo duo dolores et ea rebum. Stet clita kasd gubergren, no sea takimata sanctus est Lorem ipsum dolor sit amet.</p>
  </div>

  <div class="signer-name">KHALID ALMANSOUR</div>
  <div class="signer-role">Business Development Director</div>

  <div class="letter-footer">
    <div class="contact">M : 966500012345</div>
    <div class="contact">E : k.mansour@lumenra.sa &nbsp;|&nbsp; www.lumenra.sa</div>
    <div class="company">LUMENRA SYSTEMS</div>
    <div class="address">Tower 12<sup style="font-size:6px">th</sup> Floor, Corniche Rd. Al Khobar Saudi Arabia</div>
  </div>

  <div class="corner-decor"></div>
</section>

<section class="card card-en">
  <div class="card-name">KHALID ALMANSOUR</div>
  <div class="card-role">Business Development Director</div>
  <div class="wordmark"><span class="dot"></span>LUMENRA SYSTEMS</div>
  <div class="card-contact">
    <div class="phone">M : 966500012345</div>
    <div>E : k.mansour@lumenra.sa</div>
    <div>www.lumenra.sa</div>
  </div>
  <div class="card-company">LUMENRA SYSTEMS</div>
  <div class="card-address">Tower 12<sup style="font-size:5px">th</sup> Floor, Corniche Rd. Al Khobar Saudi Arabia</div>
  <div class="corner-decor"></div>
</section>

<section class="card card-ar">
  <div class="card-name arabic" lang="ar">خالد المنصور</div>
  <div class="card-role arabic" lang="ar">مدير تطوير الأعمال</div>
  <div class="wordmark"><span class="dot"></span>LUMENRA SYSTEMS</div>
  <div class="card-contact">
    <div class="phone">M : 966500012345</div>
    <div>E : k.mansour@lumenra.sa</div>
    <div>www.lumenra.sa</div>
  </div>
  <div class="card-company arabic" lang="ar">لومينرا سيستمز</div>
  <div class="card-address arabic" lang="ar">برج 12 طابق، طريق الكورنيش، الخبر، المملكة العربية السعودية</div>
  <div class="corner-decor"></div>
</section>

</body>
</html>
```